Recruitment of Trellan Staffing for the UK market

I want a website for the UK market to attract businesses and companies to come to us for Philipine labour. We want an information site that gives all information on what we do and how we can recruit Philippine labour.
This is a recruitment site for companies to contact us with their requirements for skilled workers coming from the Philipines over to the UK to work.

Target Market(s)

Uk Companies and businesses who want Philipine skilled workers

Industry/Entity Type

REcruitment

Coding

Number of Pages Required

5+ page

Font styles to use
Sans Serif

Colors
0054AA
0677BA
7BADD7
CADEEF
E8F1F8
0094D4
00A9DD
6FCCEA
C7EBF8
E9F6FB
EE7325
F08F49
F5BC92
FAE3D3
FDF4ED
EB3D1F
EC4F4E
F09395
F8D3D4
FCEDEE

Requirements
Must have
• Look professional and corperate with drop down menus for Home ,about, services,articles. training , contact us
Nice to have
• Look at Velmora recruitment- https://velmorarecruitment.example.co.uk/. This is my current site - https://www.trellanstaffing.example.com/
Should not have
• Cartoons or silly pictures , needs to be corperate looking

```html
<!DOCTYPE html>
<html lang="en">
<head>
<meta charset="utf-8">
<title>Trellan Staffing – Skilled Philippine Workers for UK Companies</title>
<link href="https://fonts.googleapis.com/css2?family=Poppins:wght@400;500;600;700;800&display=swap" rel="stylesheet">
<style>
:root{
  --orange:#ee7325;
  --orange-light:#f08f49;
  --red:#eb3d1f;
  --peach:#f5d6c0;
  --cream:#faf0ea;
  --grey-bg:#f1f1f2;
  --ink:#111111;
  --text:#333333;
  --white:#ffffff;
  --black:#050505;
  --brand:#8e1f1f;
}
*{margin:0;padding:0;box-sizing:border-box}
html,body{width:1200px;height:3841px;overflow:hidden}
body{font-family:'Poppins',sans-serif;color:var(--text);background:var(--white);position:relative}
.abs{position:absolute}
.btn{position:absolute;background:var(--orange);color:var(--white);font-size:16px;display:flex;align-items:center;justify-content:center;font-weight:400}
.photo{position:absolute}
h2.section-title{position:absolute;font-weight:700;color:var(--ink);font-size:37px;line-height:1.1}
p.copy{position:absolute;font-size:15px;line-height:25.5px;color:var(--text)}

/* header */
.site-header{position:absolute;left:0;top:0;width:1200px;height:85px;background:var(--white)}
.logo{position:absolute;left:119px;top:22px;display:flex;align-items:center;gap:10px;font-weight:700;font-size:22px;color:var(--brand)}
.logo .mark{width:20px;height:20px;background:var(--brand)}
.main-nav{position:absolute;left:386px;top:33px;display:flex;gap:0;font-size:16px;color:var(--ink)}
.main-nav span{margin-right:26px}
.phone-btn{left:950px;top:21px;width:153px;height:46px;font-size:17px;gap:12px}

/* hero */
.hero{position:absolute;left:0;top:85px;width:1200px;height:514px;background:linear-gradient(100deg,#3b3f4a 0%,#5e6270 45%,#8f8f97 75%,#b5b5bb 100%)}
.hero h1{position:absolute;left:116px;top:120px;font-size:45px;font-weight:800;line-height:56px;color:var(--white)}
.hero p{position:absolute;left:116px;top:252px;width:440px;font-size:17px;line-height:26px;color:var(--white)}
.hero .btn{left:116px;top:332px;width:118px;height:45px}

/* about */
.about-title{left:604px;top:668px}
.about-copy{left:604px;top:732px;width:480px}

/* working together */
.wt-title{left:0;width:1200px;text-align:center;top:1090px;font-weight:800;font-size:37px;color:var(--ink)}
.wt-copy{position:absolute;left:200px;width:800px;top:1155px;text-align:center;font-size:15px;line-height:26px}
.service-card{position:absolute;top:1244px;width:225px;height:448px;background:linear-gradient(180deg,var(--orange) 0%,#ec5a22 60%,var(--red) 100%);color:var(--white);text-align:center}
.service-card svg{position:absolute;left:62px;top:28px}
.service-card h3{position:absolute;left:0;width:225px;top:194px;font-size:23px;font-weight:700}
.service-card p{position:absolute;left:22px;width:181px;top:242px;font-size:14px;line-height:25.5px}
.service-card .card-btn{position:absolute;left:50px;top:367px;width:117px;height:46px;border:1px solid rgba(255,255,255,.9);display:flex;align-items:center;justify-content:center;font-size:16px}

/* skilled list */
.skilled{position:absolute;left:0;top:1773px;width:1200px;height:470px;background:linear-gradient(90deg,#f6d5bd 0%,#f2d2bd 60%,#eac7b1 100%)}
.accent-block{position:absolute;background:linear-gradient(180deg,var(--orange),var(--red))}

/* sponsor */
.sponsor{position:absolute;left:0;top:2243px;width:1200px;height:447px;background:var(--cream)}
.map-frame{position:absolute;left:115px;top:2313px;width:408px;height:277px;border:2px solid var(--orange)}

/* timeline */
.timeline{position:absolute;left:0;top:2690px;width:1200px;height:470px;background:linear-gradient(90deg,#f5d4bd 0%,#f2d0b9 60%,#edc9b2 100%)}
.tick{display:inline-block;width:17px;height:17px;vertical-align:-3px;margin-right:2px}

/* contact */
.contact{position:absolute;left:0;top:3160px;width:1200px;height:450px;background:var(--grey-bg)}
.field{position:absolute;left:119px;width:465px;background:var(--white);border:1px solid #d6d6d6;border-radius:4px;font-size:14px;color:#666;padding:10px 12px}
.robot{position:absolute;left:119px;top:3522px;width:188px;height:40px;background:#f9f9f9;border:1px solid #d3d3d3;border-radius:3px;display:flex;align-items:center;gap:10px;padding-left:10px;font-size:13px;color:#555}
.robot .box{width:22px;height:22px;border:2px solid #c1c1c1;border-radius:3px;background:var(--white)}
.robot .badge{width:22px;height:22px;background:#9aa7b8;border-radius:3px;margin-left:8px}
.details-title{position:absolute;left:605px;top:3250px;font-size:24px;font-weight:700;color:var(--ink)}
.detail{position:absolute;left:605px;font-size:16px;color:var(--ink);display:flex;align-items:center;gap:6px}

/* footer */
.site-footer{position:absolute;left:0;top:3610px;width:1200px;height:231px;background:var(--black);color:var(--white)}
.footer-logo{position:absolute;left:0;width:1200px;top:44px;display:flex;justify-content:center;align-items:center;gap:10px;font-weight:700;font-size:26px;color:var(--white)}
.footer-logo .mark{width:20px;height:20px;background:var(--white)}
.social{position:absolute;left:541px;top:112px;display:flex;gap:14px}
.social span{width:21px;height:21px;border:1.5px solid var(--white);border-radius:50%}
.footer-nav{position:absolute;left:146px;top:152px;display:flex;font-size:16px}
.footer-nav span{margin-right:26px}
.footer-rule{position:absolute;left:118px;top:182px;width:978px;height:1px;background:#888}
.copyright{position:absolute;left:0;width:1200px;top:192px;text-align:center;font-size:14px;display:flex;justify-content:center;align-items:center;gap:6px}
</style>
</head>
<body>

<header class="site-header">
  <div class="logo"><span class="mark"></span>Trellan Staffing</div>
  <nav class="main-nav"><span>HOME</span><span>ABOUT</span><span>SERVICES</span><span>ARTICLES</span><span>TRAINING</span><span>CONTACT US</span></nav>
  <div class="btn phone-btn">
    <svg width="18" height="18" viewBox="0 0 24 24"><path fill="#fff" d="M6.6 10.8a15.1 15.1 0 0 0 6.6 6.6l2.2-2.2a1 1 0 0 1 1-.25 11.4 11.4 0 0 0 3.6.6 1 1 0 0 1 1 1V20a1 1 0 0 1-1 1A17 17 0 0 1 3 4a1 1 0 0 1 1-1h3.5a1 1 0 0 1 1 1c0 1.25.2 2.45.6 3.6a1 1 0 0 1-.25 1z"/></svg>
    07700900482
  </div>
</header>

<section class="hero" role="img" aria-label="Photo of smiling professional workers in an office">
  <h1>Welcome To<br>Trellan Staffing</h1>
  <p>Recruiting and placing skilled Philippine workers into UK companies</p>
  <div class="btn">Read More</div>
</section>

<div class="photo" style="left:118px;top:660px;width:209px;height:178px;background:linear-gradient(135deg,#7d8a76,#c9c2b4)" role="img" aria-label="Photo of technicians in hard hats at work"></div>
<div class="photo" style="left:334px;top:660px;width:210px;height:178px;background:linear-gradient(135deg,#4f6f9a,#d9c7a8)" role="img" aria-label="Photo of smiling workers in hard hats"></div>
<div class="photo" style="left:118px;top:845px;width:426px;height:177px;background:linear-gradient(135deg,#5f87b2,#9ab3c9 60%,#b8ad96)" role="img" aria-label="Photo of a group of smiling nurses"></div>
<h2 class="section-title about-title">About Us</h2>
<p class="copy about-copy">We source skilled workers directly from the Philippines to work in the UK. With offices , training locations and specialist recruiters we can find the highest quality individuals to add value and resources to any UK buisness. We delivery quality based on vast experience over a number of years.</p>
<div class="btn" style="left:604px;top:914px;width:117px;height:46px">Read More</div>

<h2 class="abs wt-title">WORKING TOGETHER</h2>
<p class="wt-copy">We recruit the finest talent available with our dedicated 200 strong team. Our centres are highlighted in red dots on the map..</p>

<div class="service-card" style="left:118px">
  <svg width="100" height="130" viewBox="0 0 100 130"><circle cx="50" cy="60" r="40" fill="none" stroke="#fff" stroke-width="8"/><text x="50" y="82" text-anchor="middle" font-family="Poppins,sans-serif" font-weight="700" font-size="60" fill="#fff">?</text></svg>
  <h3>What We Do</h3>
  <p>Our company has been estabilished in the Philippines for over 20 years. We have mainly</p>
  <div class="card-btn">Read More</div>
</div>
<div class="service-card" style="left:368px">
  <svg width="100" height="130" viewBox="0 0 100 130"><path fill="#fff" d="M50 14a38 36 0 1 0 16 68l18 8-6-16A36 36 0 0 0 50 14z"/><text x="50" y="72" text-anchor="middle" font-family="Poppins,sans-serif" font-weight="700" font-size="46" fill="#ee7325">?</text></svg>
  <h3>How We Help</h3>
  <p>We work with companies to find skilled workers that meet the UK requirements for Visas</p>
  <div class="card-btn">Read More</div>
</div>
<div class="service-card" style="left:618px">
  <svg width="100" height="130" viewBox="0 0 100 130"><path fill="#fff" d="M20 100 L82 38 M82 38 L46 42 M82 38 L78 74" stroke="#fff" stroke-width="12" stroke-linecap="round" stroke-linejoin="round"/></svg>
  <h3>Where to Start</h3>
  <p>We need to know what your issues are and how we can understand the personnaland work</p>
  <div class="card-btn">Read More</div>
</div>
<div class="service-card" style="left:868px">
  <svg width="100" height="130" viewBox="0 0 100 130"><path fill="#fff" d="M30 24h40a6 6 0 0 1 6 6v70a6 6 0 0 1-6 6H30a6 6 0 0 1-6-6V30a6 6 0 0 1 6-6z"/><rect x="33" y="34" width="34" height="50" fill="#ee7325"/><circle cx="50" cy="95" r="4" fill="#ee7325"/></svg>
  <h3>Contact us today</h3>
  <p>Please contact us today with your requirements , this can be care workers ,chef, welders, pipe fitters,</p>
  <div class="card-btn">Read More</div>
</div>

<section class="skilled"></section>
<h2 class="section-title" style="left:116px;top:1828px">UK Skilled Workers List</h2>
<p class="copy" style="left:119px;top:1905px;width:488px">The UK government since brexit have developed a new system based on points (similar to Australia) when recruiting from outside of the UK. Previuosly EU citizens could work in the UK without any extensive documentation or clarification of skills. This has all changed.<br>Overseas recruitment must now focus on skills that are currently short in the UK. The list is extensive and is constandly being reviewed.</p>
<div class="btn" style="left:117px;top:2129px;width:117px;height:47px">Read More</div>
<div class="accent-block" style="left:957px;top:1836px;width:125px;height:134px"></div>
<div class="photo" style="left:642px;top:1862px;width:410px;height:309px;background:linear-gradient(135deg,#3b4350,#7d858f 50%,#c9c5bd)" role="img" aria-label="Photo of a smiling professional in a busy office"></div>

<section class="sponsor"></section>
<div class="map-frame"></div>
<div class="photo" style="left:140px;top:2338px;width:410px;height:278px;background:linear-gradient(120deg,#8ab4f0 0%,#8ab4f0 35%,#9fc89a 55%,#8ab4f0 75%)" role="img" aria-label="Map of the Philippines with offices marked by red dots"></div>
<h2 class="section-title" style="left:605px;top:2342px">Sponsor Licence</h2>
<p class="copy" style="left:605px;top:2417px;width:480px">If you have areas of your business that meet the entry requirements of skilled labour your next step is to gain a sponsor licence for your business. There are different types of licences depending on the size of the business.</p>
<div class="btn" style="left:605px;top:2544px;width:117px;height:46px">Read More</div>

<section class="timeline"></section>
<h2 class="section-title" style="left:114px;top:2746px">Recruitment Timeline</h2>
<p class="copy" style="left:116px;top:2813px;width:496px">Brief us on the job profiles – this is passed on to our teams in the Philippines.<br><svg class="tick" viewBox="0 0 20 20"><circle cx="10" cy="10" r="9" fill="#3aa655"/><path d="M5.5 10.5l3 3 6-6.5" fill="none" stroke="#fff" stroke-width="2.2"/></svg>Our teams in the Philippines source suitable candidates, documentation required for each candidate will be checked and vetted by the Recruitment Team. Once deemed qualified, they will now be assessed by their Technical Interviewer .<br><svg class="tick" viewBox="0 0 20 20"><circle cx="10" cy="10" r="9" fill="#3aa655"/><path d="M5.5 10.5l3 3 6-6.5" fill="none" stroke="#fff" stroke-width="2.2"/></svg>The candidates must provide a police check as pre-requisite for recruitment process to proceed</p>
<div class="btn" style="left:117px;top:3041px;width:118px;height:46px">Read More</div>
<div class="accent-block" style="left:957px;top:2752px;width:125px;height:134px"></div>
<div class="photo" style="left:642px;top:2780px;width:410px;height:307px;background:linear-gradient(135deg,#2f3d63,#4a5a86 55%,#b9b3a8)" role="img" aria-label="Photo of a presenter speaking to a team in a meeting room"></div>

<section class="contact"></section>
<h2 class="section-title" style="left:122px;top:3203px;font-size:35px">Contact Us</h2>
<div class="field" style="top:3260px;height:40px">Your Name</div>
<div class="field" style="top:3312px;height:40px">Contact Number</div>
<div class="field" style="top:3364px;height:41px">Email</div>
<div class="field" style="top:3417px;height:89px">Message</div>
<div class="robot"><span class="box"></span>I'm not a robot<span class="badge"></span></div>
<div class="btn" style="left:465px;top:3519px;width:116px;height:45px;font-weight:500">SUBMIT</div>
<div class="details-title">Contact Details</div>
<div class="detail" style="top:3303px"><svg width="14" height="14" viewBox="0 0 24 24"><path fill="#111" d="M6.6 10.8a15.1 15.1 0 0 0 6.6 6.6l2.2-2.2a1 1 0 0 1 1-.25 11.4 11.4 0 0 0 3.6.6 1 1 0 0 1 1 1V20a1 1 0 0 1-1 1A17 17 0 0 1 3 4a1 1 0 0 1 1-1h3.5a1 1 0 0 1 1 1c0 1.25.2 2.45.6 3.6a1 1 0 0 1-.25 1z"/></svg>07700900482</div>
<div class="detail" style="top:3335px"><svg width="13" height="10" viewBox="0 0 26 20"><rect width="26" height="20" fill="#111"/><path d="M1 1l12 10L25 1" fill="none" stroke="#fff" stroke-width="2"/></svg>sales@trellanstaffing.example.com</div>
<div class="detail" style="top:3366px"><svg width="13" height="17" viewBox="0 0 20 26"><path fill="#111" d="M10 0a10 10 0 0 0-10 10c0 7.5 10 16 10 16s10-8.5 10-16A10 10 0 0 0 10 0zm0 14a4 4 0 1 1 0-8 4 4 0 0 1 0 8z"/></svg>Larkspur Gardens, Elmsby Elmsby</div>
<div class="detail" style="top:3397px;left:624px">EL4 2 United Kingdom</div>

<footer class="site-footer">
  <div class="footer-logo"><span class="mark"></span>Trellan Staffing</div>
  <div class="social"><span></span><span></span><span></span><span></span></div>
  <nav class="footer-nav"><span>HOME</span><span>ABOUT</span><span>SERVICES</span><span>ARTICLES</span><span>TRAINING</span><span>CONTACT US</span><span>TERMS AND CONDITIONS</span><span>PRIVACY POLICY</span></nav>
  <div class="footer-rule"></div>
  <div class="copyright"><svg width="18" height="18" viewBox="0 0 20 20"><circle cx="10" cy="10" r="8.5" fill="none" stroke="#ee7325" stroke-width="1.6"/><path d="M13 7.5a4 4 0 1 0 0 5" fill="none" stroke="#ee7325" stroke-width="1.6"/></svg>2023TrellanStaffing</div>
</footer>

</body>
</html>
```